Business Card Design

We need a design for business cards for our company. We have a logo. We teach EMT's and we are based out of Virginia. The information that will need to add would be, name, title, phone number, email, address. On the back of the business card would be "We help you, help others"

Target Market(s)

People that want to become EMT's

Colors

Designer to choose colors to be used in the design.

Requirements
Must have
• company logo

```html
<!DOCTYPE html>
<html lang="en">
<head>
<meta charset="utf-8">
<title>Business Card – Front and Back</title>
<link rel="stylesheet" href="https://fonts.googleapis.com/css2?family=Montserrat:wght@500;600&family=Roboto:wght@400&display=swap">
<style>
  :root {
    --backdrop: #2b2b2d;
    --card-white: #ffffff;
    --brand-red: #c01d2e;
    --brand-red-soft: #b81a2b;
    --ink-grey: #555a60;
    --rule-grey: #c9c9c9;
    --on-red: #ffffff;
  }
  * { box-sizing: border-box; margin: 0; padding: 0; }
  html, body {
    width: 1200px;
    height: 1108px;
    overflow: hidden;
    background: var(--backdrop);
  }
  .stage {
    width: 1200px;
    height: 1108px;
    display: flex;
    align-items: center;
    justify-content: center;
    gap: 80px;
  }
  .card {
    position: relative;
    width: 400px;
    height: 700px;
    border-radius: 30px;
    overflow: hidden;
  }

  /* Front */
  .card-front {
    background: var(--card-white);
    display: flex;
    flex-direction: column;
    align-items: center;
  }
  .brand {
    margin-top: 176px;
    display: flex;
    align-items: center;
    gap: 12px;
  }
  .brand-dot {
    width: 30px;
    height: 30px;
    border-radius: 50%;
    background: var(--brand-red);
  }
  .brand-name {
    font-family: "Montserrat", sans-serif;
    font-weight: 600;
    font-size: 27px;
    letter-spacing: -0.3px;
    color: var(--brand-red);
    text-transform: uppercase;
    line-height: 1.05;
  }
  .contact {
    margin-top: auto;
    margin-bottom: 96px;
    width: 240px;
    text-align: center;
    font-family: "Roboto", sans-serif;
    color: var(--ink-grey);
  }
  .person-name {
    font-family: "Montserrat", sans-serif;
    font-weight: 500;
    font-size: 24px;
    letter-spacing: -0.5px;
    color: var(--brand-red);
    text-transform: uppercase;
    white-space: nowrap;
  }
  .person-title {
    font-size: 19px;
    line-height: 1.1;
  }
  .contact-rule {
    width: 200px;
    border: 0;
    border-top: 1px solid var(--rule-grey);
    margin: 10px auto 8px;
  }
  .contact-line {
    font-size: 19px;
    line-height: 1.35;
    white-space: nowrap;
  }

  /* Back */
  .card-back {
    background: var(--brand-red);
  }
  .back-pattern {
    position: absolute;
    inset: 0;
    background: linear-gradient(160deg, var(--brand-red) 0%, var(--brand-red-soft) 100%);
  }
  .back-mark {
    position: absolute;
    left: 50%;
    top: 400px;
    width: 56px;
    height: 56px;
    margin-left: -28px;
    border-radius: 50%;
    border: 3px solid var(--on-red);
  }
  .tagline {
    position: absolute;
    left: 0;
    right: 0;
    bottom: 96px;
    text-align: center;
    font-family: "Montserrat", sans-serif;
    font-weight: 500;
    font-size: 22px;
    letter-spacing: -0.3px;
    color: var(--on-red);
    text-transform: uppercase;
  }
</style>
</head>
<body>
  <main class="stage">
    <section class="card card-front" aria-label="Card front">
      <div class="brand">
        <span class="brand-dot"></span>
        <span class="brand-name">Medic Path<br>Academy</span>
      </div>
      <div class="contact">
        <p class="person-name">Daniel Carter</p>
        <p class="person-title">Managing Director</p>
        <hr class="contact-rule">
        <p class="contact-line">555-014 2687</p>
        <p class="contact-line">info@medicpath.example</p>
        <hr class="contact-rule">
        <p class="contact-line">27 Linden Row, Suite 4</p>
        <p class="contact-line">30417, Eastfield</p>
      </div>
    </section>

    <section class="card card-back" aria-label="Card back">
      <div class="back-pattern" role="img" aria-label="Faint repeating pattern of the brand symbol on red"></div>
      <span class="back-mark"></span>
      <p class="tagline">We help you, help others</p>
    </section>
  </main>
</body>
</html>
```